Awesome business card design needed

We need a new business card design to go with our new logo.
We are a web development agency that specialises in highly complex back-end integrations as opposed to design, our customers are retailers, hotels, hospitals and any other organisation that has a large online marketing department.
Take a look at our website - www.brenoloft.com for some inspiration.
We want our new business cards to exude class, professionalism and style.
We are likely to choose a high-end card to print them on but we want the design of the card itself to really turn heads.
We have no specific colour requirements, the logo as you will see is a turquoise colour R89 G171 B167 #59aba7 but it can also be in white if you want to make the colour of the card something different.
The information on the card should be:
Name
Position
Tel
email
Potentially a double sided card could have our web address, twitter and FB links.

```html
<!DOCTYPE html>
<html lang="en">
<head>
<meta charset="utf-8">
<title>Brenoloft Business Card</title>
<link rel="stylesheet" href="https://fonts.googleapis.com/css2?family=Arimo:wght@400;700&display=swap">
<style>
  :root {
    --page: #e9e9e9;
    --steel-light: #f4f4f4;
    --steel-mid: #dcdcdc;
    --steel-dark: #c9c9c9;
    --turquoise: #59aba7;
    --ink: #3a3a3a;
    --ink-soft: #555555;
    --bar-dark: #2b2b2b;
  }
  * { box-sizing: border-box; margin: 0; padding: 0; }
  html, body { width: 1200px; height: 720px; overflow: hidden; }
  body {
    background: var(--page);
    font-family: "Arimo", Arial, sans-serif;
    display: flex;
    align-items: center;
    justify-content: center;
    gap: 60px;
  }
  .card {
    position: relative;
    width: 525px;
    height: 300px;
    background:
      repeating-linear-gradient(0deg, rgba(255,255,255,0.18) 0 1px, rgba(0,0,0,0.02) 1px 2px),
      linear-gradient(135deg, var(--steel-light) 0%, var(--steel-mid) 55%, var(--steel-dark) 100%);
    box-shadow: 0 2px 8px rgba(0,0,0,0.18);
    overflow: hidden;
  }

  /* Front */
  .front-strip { position: absolute; left: 0; top: 0; width: 34px; height: 300px; }
  .front .wordmark {
    position: absolute; left: 52px; top: 38px;
    font-size: 64px; font-weight: 700; color: var(--turquoise);
    letter-spacing: 1px; line-height: 1;
  }
  .holder { position: absolute; right: 34px; top: 112px; text-align: right; }
  .holder-name { font-size: 17px; font-weight: 700; color: var(--ink); }
  .holder-role { font-size: 13px; color: var(--ink-soft); margin-top: 2px; }
  .contact { position: absolute; left: 52px; top: 176px; font-size: 14px; color: var(--ink-soft); }
  .contact-line { display: flex; align-items: center; gap: 7px; height: 19px; }
  .contact-line svg { width: 11px; height: 11px; flex: none; }
  .address { margin-top: 12px; line-height: 18px; }

  /* Back */
  .back { display: flex; flex-direction: column; align-items: center; }
  .back .wordmark {
    margin-top: 78px;
    font-size: 76px; font-weight: 700; color: var(--turquoise);
    letter-spacing: 1px; line-height: 1;
  }
  .follow { display: flex; align-items: center; gap: 8px; margin-top: 12px; margin-left: 40px; }
  .follow-label { font-size: 18px; font-weight: 700; color: var(--ink); margin-right: 4px; }
  .social-square { width: 30px; height: 30px; border-radius: 5px; background: var(--turquoise); }
  .social-square.alt { background: #4a6a9c; }
  .site { margin-top: 10px; font-size: 17px; color: var(--ink-soft); letter-spacing: 2px; }
  .site strong { color: var(--ink); }
</style>
</head>
<body>
  <section class="card front" aria-label="Card front">
    <svg class="front-strip" viewBox="0 0 34 300" aria-hidden="true">
      <polygon points="0,0 18,0 18,60 34,80 34,300 0,300" fill="var(--turquoise)"/>
      <polygon points="0,0 18,0 18,60 34,80 34,92 0,60" fill="var(--bar-dark)"/>
    </svg>
    <div class="wordmark">brenoloft</div>
    <div class="holder">
      <div class="holder-name">Your Name</div>
      <div class="holder-role">Position</div>
    </div>
    <div class="contact">
      <div class="contact-line">
        <svg viewBox="0 0 12 12" aria-hidden="true"><circle cx="6" cy="6" r="6" fill="var(--turquoise)"/><path d="M4 3.2 L5.2 4.6 L4.6 5.3 Q5.4 6.8 6.7 7.4 L7.4 6.8 L8.8 8 L8 9 Q5 8.6 3.2 4 Z" fill="#fff"/></svg>
        <span>123-456-7890</span>
      </div>
      <div class="contact-line">
        <svg viewBox="0 0 12 12" aria-hidden="true"><circle cx="6" cy="6" r="6" fill="var(--turquoise)"/><rect x="3" y="4" width="6" height="4.2" fill="#fff"/><path d="M3 4 L6 6.4 L9 4" stroke="var(--turquoise)" stroke-width="0.7" fill="none"/></svg>
        <span>info@brenoloft.com</span>
      </div>
      <div class="contact-line">
        <svg viewBox="0 0 12 12" aria-hidden="true"><circle cx="6" cy="6" r="6" fill="var(--turquoise)"/><circle cx="6" cy="6" r="3" fill="none" stroke="#fff" stroke-width="0.8"/><path d="M3 6 H9 M6 3 V9" stroke="#fff" stroke-width="0.7"/></svg>
        <span>www.brenoloft.com</span>
      </div>
      <div class="address">Street Name, City Name<br>State Zip Code</div>
    </div>
  </section>

  <section class="card back" aria-label="Card back">
    <div class="wordmark">brenoloft</div>
    <div class="follow">
      <span class="follow-label">Follow Us On:</span>
      <span class="social-square" role="img" aria-label="Social network link"></span>
      <span class="social-square alt" role="img" aria-label="Social network link"></span>
    </div>
    <div class="site">www.<strong>brenoloft</strong>.com</div>
  </section>
</body>
</html>
```